BrivoTerna. Lantern of the Steady Harvest. Business card

Professional business card for BrivoTerna (Lantern of the Steady Harvest)
My rationale: Strategy-> Execution-> Results-> Value that lead to the BrivoTerna name: We put the Lantern of the Steady Harvest.
We deliver value to our customers helping them at defining a good strategy (cyan arrow). 90% of well formulated strategies fail due to poor execution so we also consider strategical execution very important (green arrow). Due to the execution we obtain the results (blue arrow). Finally, the results provide feedback to redefine strategy, and the new strategy has to be executed and new results obtained providing new feedback and on and on. It's like a wheel that finally, must create corporate value: value for shareholders, staholders, employees, providers...-

Target Market(s)

CEOs and steering comitees , invewrnent funds

Industry/Entity Type

Business Consultant

Contact Information for Business Card

Teodoro Vinsquel
CEO & Founder
teodoro.vinsquel@brivoterna-example.com
Mobile: +34 655.803.912
www.brivoterna-example.com

Colors

Designer to choose colors to be used in the design.

Requirements
Nice to have
• Nice to hace the words: Strategy, execution, results
• Nice to vave the claim: Lantern of the Steady Harvest
• The three colors should be shown:
• cyan for STRATEGY
• green for EXECUTION
• blue for RESULTS
Should not have
• Complete black background

```html
<!DOCTYPE html>
<html lang="en">
<head>
<meta charset="utf-8">
<title>BrivoTerna — Business Card</title>
<link href="https://fonts.googleapis.com/css2?family=Roboto:wght@400;700&display=swap" rel="stylesheet">
<style>
  :root {
    --stage: #3a332e;
    --card: #0e0e0f;
    --card-edge: #1a1a1c;
    --brand-blue: #1d3fae;
    --name-blue: #2146c0;
    --text-grey: #b9b9bb;
    --silver: #d8d8da;
    --divider: #2a2a2d;
  }
  * { box-sizing: border-box; margin: 0; padding: 0; }
  html, body {
    width: 1200px; height: 844px; overflow: hidden;
    background: var(--stage);
    font-family: "Roboto", Arial, sans-serif;
  }
  .stage {
    width: 1200px; height: 844px;
    display: flex; align-items: center; justify-content: center; gap: 40px;
  }
  .card {
    width: 540px; height: 310px;
    background: var(--card);
    border: 1px solid var(--card-edge);
    box-shadow: 0 10px 30px rgba(0,0,0,.45);
    position: relative;
  }
  /* Contact side */
  .card--contact { display: flex; }
  .brand-block {
    width: 238px; border-right: 1px solid var(--divider);
    display: flex; flex-direction: column; align-items: center; justify-content: center; gap: 16px;
  }
  .brand-dot { width: 34px; height: 34px; border-radius: 50%; background: var(--brand-blue); }
  .brand-name { color: var(--brand-blue); font-weight: 700; font-size: 34px; letter-spacing: -0.5px; }
  .details { padding: 48px 0 0 26px; }
  .person-name { color: var(--name-blue); font-size: 22px; font-weight: 400; }
  .person-role { color: var(--text-grey); font-size: 13px; margin-top: 4px; }
  .contact-list { list-style: none; margin-top: 44px; }
  .contact-list li {
    display: flex; align-items: center; gap: 8px;
    color: var(--text-grey); font-size: 12.5px; line-height: 20px;
  }
  .contact-list svg { width: 12px; height: 12px; flex: none; fill: var(--brand-blue); }
  /* Brand side */
  .card--brand {
    display: flex; flex-direction: column; align-items: center; justify-content: center;
  }
  .brand-name--silver { color: var(--silver); font-size: 46px; }
  .brand-pillars {
    color: var(--silver); font-size: 12px; letter-spacing: 1.2px; text-transform: uppercase; margin-top: 6px;
  }
  .brand-rule { width: 300px; height: 1px; background: var(--divider); margin: 24px 0 18px; }
  .brand-claim {
    color: var(--silver); font-size: 13px; letter-spacing: 1.2px; text-transform: uppercase;
  }
</style>
</head>
<body>
<main class="stage">
  <section class="card card--contact">
    <div class="brand-block">
      <span class="brand-dot"></span>
      <span class="brand-name">BrivoTerna</span>
    </div>
    <div class="details">
      <h1 class="person-name">Teodoro Vinsquel</h1>
      <p class="person-role">CEO &amp; Founder</p>
      <ul class="contact-list">
        <li><svg viewBox="0 0 12 12" aria-hidden="true"><path d="M2.5 1h2l1 2.5-1.3 1a6 6 0 0 0 3.3 3.3l1-1.3 2.5 1v2c0 .6-.5 1-1 1A9.5 9.5 0 0 1 1.5 2c0-.5.4-1 1-1z"/></svg>+34 655.803.912</li>
        <li><svg viewBox="0 0 12 12" aria-hidden="true"><path d="M1 2.5h10v7H1z M1.3 2.8 6 6.5l4.7-3.7" /></svg>teodoro.vinsquel@brivoterna-example.com</li>
        <li><svg viewBox="0 0 12 12" aria-hidden="true"><circle cx="6" cy="6" r="5"/></svg>www.brivoterna-example.com</li>
      </ul>
    </div>
  </section>

  <section class="card card--brand">
    <span class="brand-name brand-name--silver">BrivoTerna</span>
    <p class="brand-pillars">Strategy, Execution, Results</p>
    <div class="brand-rule"></div>
    <p class="brand-claim">Lantern of the Steady Harvest</p>
  </section>
</main>
</body>
</html>
```